LHP Regal Business Card Design 2020

Your Manor Steward is looking for a business card that is clean and straight to the point but still looks high-end and attractive. We are a team comprised of management and field professionals focused on the high-end residential marketplace. We serve homeowners and trade professionals directly based out of the Metrowest/Boston area. We provide client services as well as construction/renovation services.
We are aiming for a black and white feel (white background and black text) and a matte finish with rounded edges.

We want to emphasis our vision of "Properties - Projects - Partners".
Dana Pellham is the president of LHP

Please include the following areas we service: Boston/Cape/Newport
Please make sure to include Dana's mobile (555) 213 4480 & office number (555) 640 1937, email dana@yourmanorsteward.example and website www.yourmanorsteward.example

Colors

Designer to choose only greyscale colors for use in the design.

Requirements
Must have
• Include "Properties - Projects - Partners" in design

Include "After Hours Emergency Support # 1800 555 0142" with icon

```html
<!DOCTYPE html>
<html lang="en">
<head>
<meta charset="utf-8">
<title>LHP Business Card</title>
<link href="https://fonts.googleapis.com/css2?family=Open+Sans:wght@400;600;700;800&display=swap" rel="stylesheet">
<style>
  :root {
    --page: #e6e6e6;
    --card-dark: #2f2f2f;
    --card-light: #f4f4f4;
    --ink: #2b2b2b;
    --ink-soft: #3a3a3a;
    --mark-on-dark: #5a5a5a;
    --rule: #444444;
    --band: #333333;
    --band-accent: #666666;
    --on-dark: #eeeeee;
  }
  * { box-sizing: border-box; margin: 0; padding: 0; }
  html, body { width: 1200px; height: 960px; overflow: hidden; }
  body {
    background: var(--page);
    font-family: "Open Sans", Arial, sans-serif;
    color: var(--ink);
    position: relative;
  }
  .card {
    position: absolute;
    left: 307px;
    width: 586px;
    height: 335px;
    border-radius: 22px;
    overflow: hidden;
  }
  .card--front { top: 120px; background: var(--card-dark); }
  .card--back { top: 506px; background: var(--card-light); }

  .front-mark {
    position: absolute;
    left: 0; right: 0; top: 88px;
    text-align: center;
    font-weight: 800;
    font-size: 132px;
    line-height: 1;
    letter-spacing: -2px;
    color: var(--mark-on-dark);
  }
  .front-tagline {
    position: absolute;
    left: 0; right: 0; top: 288px;
    text-align: center;
    font-size: 14.5px;
    letter-spacing: 1.6px;
    color: var(--on-dark);
  }

  .back-brand { position: absolute; left: 38px; top: 40px; }
  .back-brand__mark {
    font-weight: 800;
    font-size: 62px;
    line-height: 1;
    letter-spacing: -1px;
    color: var(--ink);
  }
  .back-brand__name {
    margin-top: 16px;
    font-weight: 700;
    font-size: 11.5px;
    letter-spacing: 1.2px;
    color: var(--ink);
  }

  .person { position: absolute; right: 38px; top: 144px; text-align: right; }
  .person__name { font-weight: 700; font-size: 17px; letter-spacing: 0.3px; }
  .person__title { font-size: 13.5px; margin-top: 1px; color: var(--ink-soft); }

  .rule {
    position: absolute;
    left: 36px; right: 36px; top: 194px;
    height: 1.5px; background: var(--rule);
  }

  .contacts {
    position: absolute; left: 36px; top: 208px;
    list-style: none;
    font-size: 14px; color: var(--ink-soft);
  }
  .contacts li { display: flex; align-items: center; height: 19.5px; }
  .contacts svg { width: 14px; height: 14px; margin-right: 6px; flex: none; }

  .areas {
    position: absolute; right: 38px; top: 266px;
    font-size: 14px; letter-spacing: 0.5px; color: var(--ink-soft);
  }

  .band {
    position: absolute; left: 0; right: 0; bottom: 0;
    height: 32px; background: var(--band);
  }
  .band__accent {
    position: absolute; right: 0; top: 0; bottom: 0; width: 130px;
    background: var(--band-accent);
    clip-path: polygon(22px 0, 100% 0, 100% 100%, 0 100%);
  }
  .band__site {
    position: absolute; left: 36px; top: 6px;
    font-size: 14px; letter-spacing: 1px; color: var(--on-dark);
  }
  .band__mark {
    position: absolute; right: 38px; top: 0;
    font-weight: 800; font-size: 26px; line-height: 32px;
    color: #ffffff;
  }
</style>
</head>
<body>
  <section class="card card--front" aria-label="Card front">
    <div class="front-mark">LHP</div>
    <p class="front-tagline">PROPERTIES - PROJECTS - PARTNERS</p>
  </section>

  <section class="card card--back" aria-label="Card back">
    <div class="back-brand">
      <div class="back-brand__mark">LHP</div>
      <div class="back-brand__name">YOUR MANOR STEWARD</div>
    </div>

    <div class="person">
      <div class="person__name">DANA PELLHAM</div>
      <div class="person__title">President</div>
    </div>

    <div class="rule"></div>

    <ul class="contacts">
      <li>
        <svg viewBox="0 0 14 14" aria-hidden="true"><rect x="3.5" y="0.8" width="7" height="12.4" rx="1.2" fill="none" stroke="#2b2b2b" stroke-width="1.4"/><rect x="5.5" y="10.3" width="3" height="1" fill="#2b2b2b"/></svg>
        (555) 213 4480
      </li>
      <li>
        <svg viewBox="0 0 14 14" aria-hidden="true"><path d="M3 1 L5.3 3.6 L4 5.2 C4.8 7 6.8 9 8.8 9.9 L10.4 8.6 L13 11 L11.4 12.8 C7 12.6 1.4 7 1.2 2.6 Z" fill="#2b2b2b"/></svg>
        (555) 640 1937
      </li>
      <li>
        <svg viewBox="0 0 14 14" aria-hidden="true"><path d="M4 12 V8 a3 3 0 0 1 6 0 V12 Z" fill="#2b2b2b"/><rect x="2.5" y="12" width="9" height="1.6" fill="#2b2b2b"/><path d="M7 0.5 V2.6 M2 2.5 L3.4 3.9 M12 2.5 L10.6 3.9 M0.3 6.8 H2.2 M11.8 6.8 H13.7" stroke="#2b2b2b" stroke-width="1.1"/></svg>
        (800) 555 0142
      </li>
      <li>
        <svg viewBox="0 0 14 14" aria-hidden="true"><rect x="1" y="3" width="12" height="8.5" fill="none" stroke="#2b2b2b" stroke-width="1.3"/><path d="M1 3.3 L7 8 L13 3.3" fill="none" stroke="#2b2b2b" stroke-width="1.3"/></svg>
        dana@yourmanorsteward.example
      </li>
    </ul>

    <div class="areas">BOSTON | CAPE | NEWPORT</div>

    <div class="band">
      <div class="band__accent"></div>
      <span class="band__site">yourmanorsteward.example</span>
      <span class="band__mark">LHP</span>
    </div>
  </section>
</body>
</html>
```